New letter head for Air Conditioning business

We need a new professional letter head design to suit our new re-branded air conditioning business. Our new logo is attached

```html
<!DOCTYPE html>
<html lang="en">
<head>
<meta charset="utf-8">
<title>Norvale Letterhead</title>
<link href="https://fonts.googleapis.com/css2?family=Poppins:wght@400;500;600;700&display=swap" rel="stylesheet">
<style>
  :root {
    --backdrop: #e4e4e4;
    --paper: #ffffff;
    --ink: #1b1b1b;
    --charcoal: #414042;
    --coral: #ef6b5f;
  }
  * { margin: 0; padding: 0; box-sizing: border-box; }
  html, body {
    width: 1200px; height: 1200px; overflow: hidden;
    background: var(--backdrop);
    font-family: "Poppins", sans-serif;
    color: var(--ink);
  }
  .letterhead {
    position: absolute; left: 197px; top: 30px;
    width: 806px; height: 1140px;
    background: var(--paper);
    box-shadow: 0 4px 18px rgba(0,0,0,0.12);
    overflow: hidden;
  }
  .brand {
    position: absolute; left: 66px; top: 98px;
    display: flex; align-items: center; gap: 14px;
  }
  .brand-mark {
    width: 44px; height: 44px; border-radius: 50%;
    background: var(--charcoal);
  }
  .brand-name {
    font-size: 30px; font-weight: 600; letter-spacing: 3px;
    color: var(--charcoal);
  }
  .recipient-name, .letter-date {
    position: absolute; top: 230px;
    font-size: 20px; font-weight: 700;
  }
  .recipient-name { left: 60px; }
  .letter-date { right: 50px; }
  .recipient-address {
    position: absolute; left: 60px; top: 267px;
    font-size: 20px; font-weight: 400;
  }
  .letter-body {
    position: absolute; left: 55px; right: 50px; top: 330px;
    font-size: 15px; line-height: 19px; text-align: justify;
  }
  .letter-body p + p { margin-top: 26px; }
  .sign-off {
    position: absolute; left: 60px; top: 670px;
    font-size: 20px;
  }
  .signature {
    position: absolute; left: 55px; top: 728px;
    width: 170px; height: 56px;
    background: linear-gradient(90deg, #f0f0f0, #f7f7f7);
    border-radius: 4px;
  }
  .signatory {
    position: absolute; left: 55px; top: 812px;
    font-size: 20px; font-weight: 500; line-height: 36px;
  }
  .contact-list {
    position: absolute; right: 48px; top: 860px;
    list-style: none;
  }
  .contact-item {
    display: flex; align-items: center; justify-content: flex-end;
    gap: 16px; text-align: right;
  }
  .contact-item + .contact-item { margin-top: 18px; }
  .contact-phone { font-size: 17px; line-height: 19px; }
  .contact-text { font-size: 14px; }
  .contact-icon { width: 36px; height: 36px; flex: none; }
  .footer-bar-dark {
    position: absolute; left: 0; bottom: 0;
    width: 448px; height: 46px;
    background: var(--charcoal);
  }
  .footer-bar-accent {
    position: absolute; left: 448px; right: 0; bottom: 0;
    height: 78px;
    background: var(--coral);
  }
</style>
</head>
<body>
  <main class="letterhead">
    <header class="brand">
      <span class="brand-mark"></span>
      <span class="brand-name">NORVALE</span>
    </header>

    <div class="recipient-name">Your&nbsp; Name Here</div>
    <div class="letter-date">Date : 4.6.2021</div>
    <div class="recipient-address">Address</div>

    <section class="letter-body">
      <p>Lorem ipsum dolor sit amet, consectetur adipiscing elit. Nam pretium quam eget feugiat tincidunt. Nullam consequat mi vitae pharetra sagittis. Suspendisse porta placerat velit, ac condimentum felis molestie in. Nullam eget velit in erat consectetur semper vitae ac nisi. Donec et lectus ut purus aliquam pulvinar non in arcu. Vestibulum et turpis a nisl placerat euismod. Aliquam eu quam augue. Cras consectetur, velit ut semper aliquam, odio tortor suscipit nulla, et vulputate dui risus at ante. Maecenas ac dignissim ex. Pellentesque in dignissim massa. Fusce at posuere lorem. Vivamus molestie nisl ac nisi rhoncus vulputate. Aenean augue arcu, maximus ut consequat in, lobortis sit amet lectus. Suspendisse dapibus auctor quam, sed tempor orci euismod accumsan. In hac habitasse platea dictumst. Suspendisse ut enim metus.</p>
      <p>Nullam at mi eros. Lorem ipsum dolor sit amet, consectetur adipiscing elit. Vestibulum tempus, sem id pharetra ultrices, magna nulla aliquet sapien, ac fringilla odio tortor in eros. Duis a urna sem. Nunc ac purus mattis, pharetra urna quis, ultrices quam. Proin ac sollicitudin dolor, ac feugiat turpis. Sed aliquet ornare nisi, vitae finibus tortor vehicula auctor.</p>
    </section>

    <div class="sign-off">Regards</div>
    <div class="signature" role="img" aria-label="Handwritten signature"></div>
    <div class="signatory">
      <div>Your Name Here</div>
      <div>Designation Here</div>
    </div>

    <ul class="contact-list">
      <li class="contact-item">
        <span class="contact-phone">+12345689<br>+12345689</span>
        <svg class="contact-icon" viewBox="0 0 36 36" aria-hidden="true">
          <circle cx="18" cy="18" r="18" fill="var(--coral)"/>
          <path d="M12 10c1-1 2.5-1 3 .3l1.3 3c.3.8 0 1.5-.6 2l-1 .8c.8 1.8 2.2 3.3 4 4.2l.9-1c.5-.6 1.3-.8 2-.5l3 1.3c1.2.5 1.3 2 .3 3l-1.2 1.2c-1.3 1.2-3.3 1.3-5.5 0-3.6-2-6.4-5-8-8.5-1-2.2-.8-4 .5-5.2z" fill="#fff"/>
        </svg>
      </li>
      <li class="contact-item">
        <span class="contact-text">www.yourwebsite.com</span>
        <svg class="contact-icon" viewBox="0 0 36 36" aria-hidden="true">
          <g fill="none" stroke="var(--coral)" stroke-width="2">
            <circle cx="18" cy="18" r="15"/>
            <ellipse cx="18" cy="18" rx="6.5" ry="15"/>
            <line x1="18" y1="3" x2="18" y2="33"/>
            <line x1="3" y1="18" x2="33" y2="18"/>
            <path d="M6 10.5h24M6 25.5h24"/>
          </g>
        </svg>
      </li>
      <li class="contact-item">
        <span class="contact-text">yourgmail@.com</span>
        <svg class="contact-icon" viewBox="0 0 36 36" aria-hidden="true">
          <circle cx="18" cy="18" r="18" fill="var(--coral)"/>
          <rect x="9" y="12" width="18" height="12" fill="none" stroke="#fff" stroke-width="1.5"/>
          <path d="M9 12l9 7 9-7M9 24l6.5-6M27 24l-6.5-6" fill="none" stroke="#fff" stroke-width="1.5"/>
        </svg>
      </li>
    </ul>

    <div class="footer-bar-dark"></div>
    <div class="footer-bar-accent"></div>
  </main>
</body>
</html>
```